Kestrelway Financial Plans

I am looking for a complete resdesign of my small financial presentation. This is a Word Doc/PDF that I print off when meeting with people in private. I often present my "two pager" that I have been using for years and years. It tells them the basics of what I do, how I help people and foundational financial principles.

I have recently gone out on my own in business and have completely rebranded. This presentation is my most used tool, so it is the first of many things I would like to redo. I am hoping it will somehow coordinate with the colors of my business, not necessarily the EXACT same 3 colors everywhere, but have the design colors compliment.

I've uploaded all my logo designs, as well as the current "two-pager". I am not against it going to 3 pages if needed. As it will still land on 2 pages with duplex printing.

It has always been VERY simple. I am wanting it built into a more professional and design specific format, to show off my branding, without being over cluttered.

I am completely open to ANY graphics changes. Obviously some are very novice, the house on the last page has always been overly simplified.

```html
<!DOCTYPE html>
<html lang="en">
<head>
<meta charset="utf-8">
<title>Kestrelway Financial Plans – The Financial Challenge</title>
<link rel="stylesheet" href="https://fonts.googleapis.com/css2?family=Montserrat:wght@500;600;700;800&family=Oswald:wght@600&display=swap">
<style>
  :root{
    --navy:#16223a;
    --navy-deep:#11262e;
    --green:#0aa83f;
    --grey:#8a8d91;
    --grey-col:#6f7174;
    --grey-row:#55585c;
    --blue:#3a6cc2;
    --blue-line:#8fb0db;
    --tile:#c4dcf1;
    --red:#a8161b;
    --pill:#e31e24;
    --white:#ffffff;
  }
  html,body{margin:0;padding:0;overflow:hidden;background:#e9e7e6;}
  .canvas{position:relative;width:723px;height:1200px;overflow:hidden;font-family:"Montserrat",Arial,sans-serif;color:var(--navy);}
  .sheet{position:absolute;left:0;width:723px;height:600px;overflow:hidden;}
  .sheet-front{top:0;background:var(--white);}
  .sheet-back{top:600px;background:var(--navy);}
  .abs{position:absolute;}
  p,h1,h2,ul{margin:0;}

  /* front: header */
  .brand{left:40px;top:12px;text-align:center;font-weight:700;color:var(--navy);}
  .brand-name{font-size:26px;letter-spacing:1px;line-height:1;}
  .brand-sub{font-size:9px;letter-spacing:3px;margin-top:5px;}
  .title-band{left:0;top:62px;width:723px;height:78px;background:var(--navy);}
  .title{left:40px;top:68px;font-weight:800;line-height:0.98;color:var(--white);}
  .title .t-the{font-size:18px;}
  .title .t-fin{font-size:22px;color:var(--green);}
  .title .t-cha{font-size:22px;}
  .photo-ring{left:560px;top:6px;width:140px;height:140px;border-radius:50%;background:var(--grey);}
  .photo{left:577px;top:23px;width:106px;height:106px;border-radius:50%;
    background:radial-gradient(circle at 40% 40%,#f4f6f8,#c7ced6 70%,#9aa6b3);}

  /* front: challenge */
  .challenge{left:0;top:140px;width:723px;height:194px;background:var(--green);}
  .badge{left:36px;width:52px;height:52px;border-radius:50%;background:var(--navy);}
  .badge span{position:absolute;left:4px;top:4px;width:44px;height:44px;border-radius:50%;background:var(--white);
    display:flex;align-items:center;justify-content:center;font-family:"Oswald",Arial,sans-serif;font-weight:600;font-size:8.5px;color:var(--navy);}
  .stat{left:110px;width:585px;color:var(--white);font-size:7.6px;font-weight:600;line-height:1.25;text-transform:uppercase;}

  /* front: section tabs */
  .rule{left:0;width:723px;height:3px;}
  .tab{height:22px;color:var(--white);font-size:10px;font-weight:700;display:flex;align-items:center;justify-content:center;letter-spacing:.3px;}
  .tab-green{left:231px;top:338px;width:262px;background:var(--green);clip-path:polygon(0 0,100% 0,92% 100%,8% 100%);}
  .tab-navy{left:241px;top:488px;width:242px;background:var(--navy);clip-path:polygon(0 0,100% 0,92% 100%,8% 100%);}

  /* front: services */
  .service{top:366px;text-align:center;}
  .service svg{display:block;margin:0 auto;}
  .svc-label{font-size:7.2px;font-weight:700;margin-top:4px;white-space:nowrap;}
  .svc-note{color:var(--green);font-size:7px;font-weight:700;line-height:1.3;}
  .divider{top:414px;width:1px;height:66px;background:var(--blue-line);}
  .between{left:96px;top:368px;font-size:7.5px;font-weight:600;line-height:1.2;}

  /* front: progress */
  .savings-label{left:132px;top:546px;font-size:12px;font-weight:600;}
  .checklist{left:238px;top:520px;padding:0;list-style:none;}
  .checklist li{display:flex;align-items:center;font-size:8.5px;font-weight:600;margin-bottom:8px;}
  .checklist li::before{content:"";width:9px;height:9px;border:1.3px solid var(--green);margin-right:9px;}
  .partners{left:470px;top:514px;width:230px;display:grid;grid-template-columns:1fr 1fr;gap:3px;}
  .partners div{height:14px;background:var(--tile);}

  /* back: rule of 72 */
  .r72-title{left:0;top:610px;width:723px;text-align:center;color:var(--white);font-size:16px;font-weight:700;letter-spacing:.5px;}
  .r72-col{top:640px;width:155px;display:flex;flex-direction:column;gap:4px;}
  .r72-row{height:17px;display:flex;justify-content:space-between;align-items:center;padding:0 8px;
    font-size:7.5px;font-weight:700;color:var(--white);background:var(--grey-row);}
  .r72-row.head{background:var(--green);}
  .r72-double{top:812px;width:155px;height:26px;background:var(--green);color:var(--white);
    font-size:7.5px;font-weight:700;line-height:1.2;display:flex;align-items:center;justify-content:center;text-align:center;}

  /* back: structure */
  .structure{left:0;top:850px;width:723px;height:274px;background:var(--green);}
  .structure-title{left:0;top:894px;width:723px;text-align:center;color:var(--white);font-size:22px;font-weight:800;letter-spacing:.5px;}
  .pillar{top:950px;width:161px;height:124px;color:var(--white);text-align:center;}
  .pillar-grey{background:var(--grey-col);}
  .pillar-navy{background:var(--navy);}
  .pillar h3{margin:8px 0 6px;font-size:13px;font-weight:700;}
  .pillar p{font-size:8.3px;font-weight:600;line-height:1.25;padding:0 6px;}
  .pill{position:absolute;left:40px;bottom:8px;width:81px;height:14px;border-radius:7px;background:var(--pill);
    font-size:9px;font-weight:800;display:flex;align-items:center;justify-content:center;}
  .support-bar{left:40px;top:1080px;width:637px;height:28px;background:var(--navy);border:3px solid var(--grey);
    display:flex;align-items:center;color:var(--white);font-size:8.5px;font-weight:700;line-height:1.2;text-align:center;}
  .support-bar div{flex:1;}

  /* back: footer */
  .footer{left:0;top:1124px;width:723px;height:76px;background:var(--navy-deep);}
  .footer-brand{left:170px;top:1142px;width:240px;text-align:center;color:var(--white);font-weight:700;}
  .footer-brand .brand-name{font-size:22px;}
  .footer-brand .brand-sub{font-size:8px;letter-spacing:3px;margin-top:4px;}
  .footer-divider{left:440px;top:1136px;width:1px;height:52px;background:var(--grey);}
</style>
</head>
<body>
<main class="canvas">

  <!-- FRONT SHEET -->
  <section class="sheet sheet-front">
    <header class="abs brand">
      <div class="brand-name">KESTRELWAY</div>
      <div class="brand-sub">FINANCIAL PLANS</div>
    </header>

    <div class="abs title-band"></div>
    <h1 class="abs title">
      <div class="t-the">THE</div>
      <div class="t-fin">FINANCIAL</div>
      <div class="t-cha">CHALLENGE</div>
    </h1>

    <div class="abs photo-ring"></div>
    <div class="abs photo" role="img" aria-label="Photo of hands reviewing financial charts on a clipboard"></div>

    <div class="abs challenge"></div>
    <div class="abs badge" style="top:148px"><span>SAVINGS</span></div>
    <div class="abs badge" style="top:210px"><span>DEBT</span></div>
    <div class="abs badge" style="top:272px"><span>INSURANCE</span></div>

    <p class="abs stat" style="top:148px">49% of Canadian employees are living paycheque to paycheque. 25% of Canadians are unable to cover an unexpected $500 expense - National Data Office (Feb 2023)</p>
    <p class="abs stat" style="top:172px">49% of Canadian employees are living paycheque to paycheque. 25% of Canadians are unable to cover an unexpected $500 expense - National Data Office (Feb 2023)</p>
    <p class="abs stat" style="top:208px">The average Canadian has $22,131 in consumer debt, which excludes mortgages.<br>- Ledgerline (Aug 2024)</p>
    <p class="abs stat" style="top:232px">Over 55% of Canadians hold credit card debt and the total Canadian household debt has increased to $2.52 trillion, including consumer credit, mortgage and non-mortgage loans. - Northern Lenders Assoc. (Aug 2024)</p>
    <p class="abs stat" style="top:266px">45% of Canadians do not have individual life insurance coverage, but 48% say their families would face financial trouble within 6 months of losing someone.<br>- Coverwise Intl. (Apr 2023)</p>
    <p class="abs stat" style="top:300px">2-in-5 Canadians (43% women / 44% men) will be diagnosed with a form of cancer or other critical illness during their lifetime. Every 7 seconds.<br>- Health Facts Registry (June 2024)</p>

    <div class="abs rule" style="top:338px;background:var(--green)"></div>
    <h2 class="abs tab tab-green">WHO ARE WE AND WHAT DO WE DO?</h2>

    <div class="abs service" style="left:20px;width:80px">
      <svg width="40" height="36" viewBox="0 0 60 54"><rect x="10" y="8" width="46" height="26" rx="2" fill="none" stroke="var(--blue)" stroke-width="2.5" transform="rotate(-8 33 21)"/><rect x="4" y="18" width="48" height="28" rx="2" fill="var(--white)" stroke="var(--blue)" stroke-width="3"/><circle cx="28" cy="32" r="6" fill="var(--blue)"/><circle cx="12" cy="32" r="2.5" fill="var(--blue)"/><circle cx="44" cy="32" r="2.5" fill="var(--blue)"/></svg>
      <div class="svc-label">CASH FLOW</div>
      <div class="svc-note" style="margin-top:10px">ANALYZE</div>
      <div class="svc-note" style="margin-top:12px">FREE UP</div>
    </div>
    <div class="abs between">$400/<br>$600<br><svg width="22" height="8"><path d="M1 4h17M14 1l4 3-4 3" stroke="var(--navy)" stroke-width="1.3" fill="none"/></svg></div>

    <div class="abs service" style="left:126px;width:124px">
      <svg width="40" height="36" viewBox="0 0 60 54"><path d="M6 26 A24 22 0 0 1 54 26 Q48 20 42 26 Q36 20 30 26 Q24 20 18 26 Q12 20 6 26Z" fill="var(--blue)"/><path d="M30 26v20a4 4 0 0 1-8 0" stroke="var(--navy)" stroke-width="2.5" fill="none"/></svg>
      <div class="svc-label">CASH FLOW PROTECTION</div>
      <div class="svc-note" style="margin-top:10px">INCOME PROTECTION</div>
      <svg width="100" height="14"><path d="M38 1 L33 12M30 9l3 3 3-2M62 1 L67 12M64 10l3 2 3-3" stroke="var(--blue)" stroke-width="1.2" fill="none"/></svg>
      <div style="display:flex;justify-content:space-around"><div class="svc-note">LIFE<br>INSURANCE</div><div class="svc-note">CI/DI<br>INSURANCE</div></div>
    </div>

    <div class="abs service" style="left:256px;width:100px">
      <svg width="40" height="36" viewBox="0 0 60 54"><rect x="6" y="10" width="48" height="32" rx="3" fill="none" stroke="var(--blue)" stroke-width="3"/><rect x="6" y="17" width="48" height="6" fill="var(--blue)"/><rect x="12" y="30" width="16" height="4" fill="var(--blue)"/><path d="M8 48 L52 4" stroke="var(--blue)" stroke-width="3"/></svg>
      <div class="svc-label">DEBT MANAGEMENT</div>
      <div class="svc-note" style="margin-top:10px">20%</div>
      <svg width="10" height="14"><path d="M5 1v11M2 9l3 3 3-3" stroke="var(--blue)" stroke-width="1.2" fill="none"/></svg>
      <div class="svc-note">6%-7%</div>
    </div>

    <div class="abs service" style="left:362px;width:104px">
      <svg width="42" height="36" viewBox="0 0 64 54"><path d="M4 14h36v28H4zM40 22h12l8 10v10H40z" fill="var(--blue)"/><circle cx="16" cy="44" r="5" fill="var(--white)" stroke="var(--navy)" stroke-width="2"/><circle cx="48" cy="44" r="5" fill="var(--white)" stroke="var(--navy)" stroke-width="2"/><path d="M22 20v16M14 28h16" stroke="var(--white)" stroke-width="4"/><path d="M44 25h7l5 6H44z" fill="var(--white)"/></svg>
      <div class="svc-label">EMERGENCY FUND</div>
      <div class="svc-note" style="margin-top:10px">IF/WHEN</div>
      <div class="svc-note" style="margin-top:8px">3/6<br>MONTHS</div>
    </div>

    <div class="abs service" style="left:472px;width:110px">
      <svg width="40" height="36" viewBox="0 0 60 54"><ellipse cx="30" cy="28" rx="22" ry="17" fill="var(--blue)"/><circle cx="52" cy="26" r="5" fill="var(--blue)"/><rect x="16" y="40" width="7" height="10" fill="var(--blue)"/><rect x="36" y="40" width="7" height="10" fill="var(--blue)"/><rect x="24" y="8" width="12" height="3" fill="var(--navy)"/></svg>
      <div class="svc-label">BUILD WEALTH</div>
      <div class="svc-note" style="margin-top:10px">FINANCIAL<br>INDEPENDENCE<br>NUMBER (F.I.N)</div>
      <svg width="22" height="17" viewBox="0 0 30 24" style="margin-top:3px"><rect x="3" y="9" width="24" height="13" fill="var(--blue)"/><path d="M3 9 Q15 -2 27 9Z" fill="var(--navy)"/><rect x="13" y="12" width="4" height="5" fill="var(--white)"/></svg>
    </div>

    <div class="abs service" style="left:590px;width:110px">
      <svg width="40" height="36" viewBox="0 0 60 54"><rect x="10" y="6" width="40" height="42" rx="2" fill="none" stroke="var(--blue)" stroke-width="3"/><rect x="16" y="12" width="28" height="30" fill="none" stroke="var(--blue)" stroke-width="2"/><circle cx="30" cy="27" r="6" fill="none" stroke="var(--blue)" stroke-width="2.5"/><rect x="14" y="48" width="6" height="4" fill="var(--blue)"/><rect x="40" y="48" width="6" height="4" fill="var(--blue)"/></svg>
      <div class="svc-label">PRESERVE</div>
      <div class="svc-note" style="margin-top:10px">LEAVING A LEGACY</div>
      <div class="svc-note" style="margin-top:12px">WILL PREP</div>
    </div>

    <div class="abs divider" style="left:118px"></div>
    <div class="abs divider" style="left:256px"></div>
    <div class="abs divider" style="left:360px"></div>
    <div class="abs divider" style="left:468px"></div>
    <div class="abs divider" style="left:586px"></div>

    <div class="abs rule" style="top:488px;background:var(--navy)"></div>
    <h2 class="abs tab tab-navy">HOW ARE WE DOING IT?</h2>

    <svg class="abs" style="left:40px;top:512px" width="84" height="84" viewBox="-42 -42 84 84" role="img" aria-label="Pie chart of income split into living expenses, taxes, debt and savings">
      <path d="M0 0 L0 -40 A40 40 0 0 1 38.6 -10.3Z" fill="var(--green)"/>
      <path d="M0 0 L38.6 -10.3 A40 40 0 0 1 38.6 10.3Z" fill="var(--red)"/>
      <path d="M0 0 L38.6 10.3 A40 40 0 0 1 0 40Z" fill="var(--grey)"/>
      <path d="M0 0 L0 40 A40 40 0 0 1 0 -40Z" fill="var(--navy)"/>
      <text x="18" y="-12" font-size="6" font-weight="600" fill="var(--navy)" text-anchor="middle">Taxes</text>
      <text x="18" y="18" font-size="6" font-weight="600" fill="var(--navy)" text-anchor="middle">Debt</text>
      <text x="-20" y="-1" font-size="6" font-weight="600" fill="var(--white)" text-anchor="middle">Living</text>
      <text x="-20" y="6" font-size="6" font-weight="600" fill="var(--white)" text-anchor="middle">Expenses</text>
    </svg>

    <div class="abs savings-label">Savings</div>
    <svg class="abs" style="left:190px;top:551px" width="34" height="8"><path d="M1 4h28M26 1l4 3-4 3" stroke="var(--navy)" stroke-width="1.2" fill="none"/></svg>

    <ul class="abs checklist">
      <li>RETIREMENT SAVINGS</li>
      <li>CHILDREN'S EDUCATION</li>
      <li>PROPER PROTECTION</li>
      <li>FREEDOM FROM DEBT</li>
    </ul>

    <div class="abs partners" role="img" aria-label="Partner insurance carriers">
      <div></div><div></div><div></div><div></div><div></div>
      <div></div><div></div><div></div><div></div><div></div>
    </div>
  </section>

  <!-- BACK SHEET -->
  <section class="sheet sheet-back" style="top:0;height:1200px;background:transparent;pointer-events:none"></section>
  <div class="abs" style="left:0;top:600px;width:723px;height:600px;background:var(--navy)"></div>

  <h2 class="abs r72-title">RULE OF 72</h2>

  <div class="abs r72-col" style="left:40px">
    <div class="r72-row head"><span>AGE</span><span>4%</span></div>
    <div class="r72-row"><span>29</span><span>$10,000</span></div>
    <div class="r72-row"><span>47</span><span>$20,000</span></div>
    <div class="r72-row"><span>65</span><span>$40,000</span></div>
  </div>
  <div class="abs r72-col" style="left:201px">
    <div class="r72-row head"><span>AGE</span><span>6%</span></div>
    <div class="r72-row"><span>29</span><span>$10,000</span></div>
    <div class="r72-row"><span>41</span><span>$20,000</span></div>
    <div class="r72-row"><span>53</span><span>$40,000</span></div>
    <div class="r72-row"><span>65</span><span>$80,000</span></div>
  </div>
  <div class="abs r72-col" style="left:362px">
    <div class="r72-row head"><span>AGE</span><span>8%</span></div>
    <div class="r72-row"><span>29</span><span>$10,000</span></div>
    <div class="r72-row"><span>38</span><span>$20,000</span></div>
    <div class="r72-row"><span>47</span><span>$40,000</span></div>
    <div class="r72-row"><span>56</span><span>$80,000</span></div>
    <div class="r72-row"><span>56</span><span>$160,000</span></div>
  </div>
  <div class="abs r72-col" style="left:523px">
    <div class="r72-row head"><span>AGE</span><span>12%</span></div>
    <div class="r72-row"><span>29</span><span>$10,000</span></div>
    <div class="r72-row"><span>35</span><span>$20,000</span></div>
    <div class="r72-row"><span>41</span><span>$40,000</span></div>
    <div class="r72-row"><span>47</span><span>$80,000</span></div>
    <div class="r72-row"><span>53</span><span>$160,000</span></div>
    <div class="r72-row"><span>59</span><span>$320,000</span></div>
    <div class="r72-row"><span>59</span><span>$640,000</span></div>
  </div>

  <div class="abs r72-double" style="left:40px">MONEY DOUBLES<br>EVERY 18 YEARS</div>
  <div class="abs r72-double" style="left:201px">MONEY DOUBLES<br>EVERY 12 YEARS</div>
  <div class="abs r72-double" style="left:362px">MONEY DOUBLES<br>EVERY 9 YEARS</div>
  <div class="abs r72-double" style="left:523px">MONEY DOUBLES<br>EVERY 6 YEARS</div>

  <div class="abs structure"></div>
  <svg class="abs" style="left:0;top:850px" width="723" height="100"><polyline points="0,92 361.5,16 723,92" fill="none" stroke="var(--white)" stroke-width="8"/></svg>
  <h2 class="abs structure-title">STRUCTURE</h2>

  <div class="abs pillar pillar-grey" style="left:40px">
    <h3>HOME</h3>
    <p>Partner with mortgage brokers for best rates</p>
    <p style="margin-top:8px">Mortgage insurance alter-natives</p>
    <div class="pill">SELL</div>
  </div>
  <div class="abs pillar pillar-navy" style="left:201px">
    <h3>RRSP</h3>
    <p style="margin-top:10px">Tax<br>Deduction</p>
    <p style="margin-top:14px">Tax<br>Deferred</p>
    <div class="pill">100$</div>
  </div>
  <div class="abs pillar pillar-grey" style="left:362px">
    <h3>TFSA</h3>
    <p>No Tax Deductions<br>Tax Free Growth<br>2009-$95,000<br>Limit 2023-<br>47,000/YR</p>
    <div class="pill">0% TAX</div>
  </div>
  <div class="abs pillar pillar-navy" style="left:523px">
    <h3>PERM LIFE</h3>
    <p style="margin-top:10px">No Tax Deduction<br>Qualify<br>Tax Deferred<br>Growth</p>
    <div class="pill">0% TAX</div>
  </div>

  <div class="abs support-bar">
    <div>LIFE INSURANCE ILLNESS<br>CRITICAL/DISABILITY</div>
    <div>DEBT MANAGEMENT<br>CASH FLOW</div>
  </div>

  <footer class="abs footer"></footer>
  <div class="abs footer-brand">
    <div class="brand-name">KESTRELWAY</div>
    <div class="brand-sub">FINANCIAL PLANS</div>
  </div>
  <div class="abs footer-divider"></div>
  <svg class="abs" style="left:500px;top:1134px" width="56" height="56" viewBox="0 0 56 56" role="img" aria-label="No crowdfunding symbol">
    <circle cx="28" cy="28" r="24" fill="var(--white)" stroke="var(--pill)" stroke-width="5"/>
    <path d="M11 11 L45 45" stroke="var(--pill)" stroke-width="5"/>
  </svg>

</main>
</body>
</html>
```